Veldmark Supplies Business Card

Professional business card that stand out to our potential customers. Front and back with clean modern design

Industry/Entity Type

Oil and gas

Contact Information for Business Card

Name, address, website , office phone and cell number

Requirements
Must have
• Editable files for each employee

```html
<!DOCTYPE html>
<html lang="en">
<head>
<meta charset="utf-8">
<title>Veldmark Supplies Business Card</title>
<link rel="stylesheet" href="https://fonts.googleapis.com/css2?family=Bebas+Neue&family=Poppins:wght@400;700&display=swap">
<style>
  :root {
    --backdrop: #1c1c1c;
    --card-white: #ffffff;
    --card-dark: #111111;
    --brand-red: #ff0000;
    --brand-blue: #00aed1;
    --text-light: #ffffff;
  }
  * { margin: 0; padding: 0; box-sizing: border-box; }
  html, body { width: 1200px; height: 900px; overflow: hidden; }
  body {
    background: var(--backdrop);
    font-family: "Poppins", sans-serif;
    position: relative;
  }
  .card {
    position: absolute;
    left: 320px;
    width: 560px;
    height: 320px;
    overflow: hidden;
    box-shadow: 0 10px 28px rgba(0,0,0,0.6);
  }
  .card-front { top: 80px; background: var(--card-white); }
  .card-back { top: 480px; background: var(--card-dark); }
  .stripe {
    position: absolute;
    left: 0; bottom: 0;
    width: 100%;
    height: 10px;
    display: flex;
  }
  .stripe-red { width: 48%; background: var(--brand-red); }
  .stripe-blue { flex: 1; background: var(--brand-blue); }

  .brand {
    position: absolute;
    top: 0; left: 0; right: 0; bottom: 10px;
    display: flex;
    align-items: center;
    justify-content: center;
    gap: 16px;
  }
  .brand-square {
    width: 34px; height: 34px;
    background: var(--brand-red);
  }
  .brand-name {
    font-weight: 700;
    font-size: 34px;
    letter-spacing: 1px;
    text-transform: uppercase;
    color: var(--brand-red);
  }

  .person-name {
    position: absolute;
    left: 48px;
    top: 96px;
    font-family: "Bebas Neue", sans-serif;
    font-size: 40px;
    font-weight: 400;
    line-height: 1;
    color: var(--brand-red);
    letter-spacing: 0.5px;
  }
  .divider {
    position: absolute;
    left: 268px;
    top: 96px;
    width: 1px;
    height: 84px;
    background: var(--brand-blue);
  }
  .contact-list {
    position: absolute;
    left: 290px;
    top: 100px;
    list-style: none;
  }
  .contact-item {
    display: flex;
    align-items: center;
    gap: 8px;
    font-size: 15px;
    line-height: 25px;
    color: var(--text-light);
    white-space: nowrap;
  }
  .contact-icon { width: 13px; height: 13px; flex: none; }
  .address {
    position: absolute;
    left: 48px;
    top: 222px;
    font-size: 15px;
    color: var(--text-light);
    white-space: nowrap;
  }
</style>
</head>
<body>
  <section class="card card-front" aria-label="Card front">
    <div class="brand">
      <span class="brand-square"></span>
      <span class="brand-name">Veldmark Supplies</span>
    </div>
    <div class="stripe"><span class="stripe-red"></span><span class="stripe-blue"></span></div>
  </section>

  <section class="card card-back" aria-label="Card back">
    <h1 class="person-name">Daniel Harper</h1>
    <span class="divider"></span>
    <ul class="contact-list">
      <li class="contact-item">
        <svg class="contact-icon" viewBox="0 0 16 16"><path d="M3 1l3 3-2 2c1 2 4 5 6 6l2-2 3 3-2 2C7 15 1 9 1 3z" fill="none" stroke="#ff0000" stroke-width="1.6"/></svg>
        061-482 730 915
      </li>
      <li class="contact-item">
        <svg class="contact-icon" viewBox="0 0 16 16"><rect x="4" y="1" width="8" height="14" rx="1.5" fill="none" stroke="#ff0000" stroke-width="1.6"/><circle cx="8" cy="12.5" r="0.9" fill="#ff0000"/></svg>
        072-594 318 260
      </li>
      <li class="contact-item">
        <svg class="contact-icon" viewBox="0 0 16 16"><circle cx="8" cy="8" r="7" fill="#ff0000"/><path d="M1 8h14M8 1c-3 4-3 10 0 14M8 1c3 4 3 10 0 14" fill="none" stroke="#111" stroke-width="1"/></svg>
        www.veldmarksupplies.com
      </li>
    </ul>
    <p class="address">87, Harwell Road, Brakpan Industrial, 1540</p>
    <div class="stripe"><span class="stripe-red"></span><span class="stripe-blue"></span></div>
  </section>
</body>
</html>
```